LEARN Business Skills so you can Earn a good living

size of the poster is 8”x 10.75" plus 0.25" bleed.
Please leave 1 inch on the bottoum for footer
I want a design a poster that will attract people's attention.
I appreciate a creative ad however the ad should not take away from being able to clearly read the text.
-I also appreciate a simple creative ad that is not too busy.
-you can use graphics, vectors, or pictures of real people.
-however, if you use real people it should be a white male that is wearing a white shirt and look like a professional person.

Target Market(s)

Potential young business people

Industry/Entity Type

education

Requirements
Must have
• easy to read the text
Nice to have
• I would like a "creative" simple ad that is easy to be read
Should not have
• pictures of women

```html
<!DOCTYPE html>
<html lang="en">
<head>
<meta charset="utf-8">
<title>Learn It To Earn It – Business Enrichment Course</title>
<link rel="stylesheet" href="https://fonts.googleapis.com/css2?family=Poppins:wght@300;400;600;700;800&display=swap">
<style>
  :root {
    --ink: #1c1c1c;
    --band: #232323;
    --white: #ffffff;
    --rule: #c9c9c9;
    --icon-fill: #6d6d6d;
    --icon-ring: #d9d9d9;
    --photo-light: #f6f6f6;
    --photo-mid: #dedede;
    --photo-grey: #b4b4b4;
    --photo-dark: #6a6a6a;
  }
  * { margin: 0; padding: 0; box-sizing: border-box; }
  html, body { width: 800px; height: 1200px; overflow: hidden; background: var(--white); }
  body { font-family: "Poppins", sans-serif; color: var(--ink); }

  .poster { position: relative; width: 800px; height: 1200px; overflow: hidden; background: var(--white); }

  .hero-photo {
    position: absolute; left: 0; top: 0; width: 800px; height: 745px;
    background:
      linear-gradient(180deg, rgba(255,255,255,0.55) 0%, rgba(255,255,255,0) 40%),
      linear-gradient(95deg, var(--photo-light) 0%, var(--photo-mid) 45%, var(--photo-grey) 68%, var(--photo-dark) 100%);
  }

  .headline { position: absolute; left: 42px; top: 52px; line-height: 1; white-space: nowrap; }
  .headline .learn { font-weight: 800; font-size: 178px; letter-spacing: -5px; display: inline-block; }
  .headline .it-light { font-weight: 300; font-size: 178px; margin-left: 22px; display: inline-block; }
  .subline { position: absolute; left: 42px; top: 236px; font-size: 96px; line-height: 1; letter-spacing: -2px; white-space: nowrap; }
  .subline .light { font-weight: 300; }
  .subline .bold { font-weight: 800; }

  .divider { position: absolute; left: 45px; top: 364px; width: 440px; height: 1px; background: var(--rule); }

  .course-title { position: absolute; left: 42px; top: 404px; font-weight: 800; line-height: 0.98; }
  .course-title .line-lg { font-size: 68px; display: block; letter-spacing: -1.5px; }
  .course-title .line-md { font-size: 49px; display: block; letter-spacing: -1px; }
  .course-title .line-course { font-size: 64px; display: block; letter-spacing: -1.5px; }
  .since { position: absolute; left: 44px; top: 600px; font-weight: 600; font-size: 30px; }

  .info-band { position: absolute; left: 0; top: 745px; width: 800px; height: 455px; background: var(--band); }

  .benefits-frame {
    position: absolute; left: 55px; top: 805px; width: 690px; height: 190px;
    border: 1.5px solid var(--icon-ring); border-radius: 18px;
  }
  .benefits-label {
    position: absolute; left: 98px; top: 783px; width: 606px; height: 48px;
    background: var(--white); border-radius: 24px; border: 5px solid var(--band);
    display: flex; align-items: center; justify-content: center;
    font-weight: 700; font-size: 28px; color: var(--ink); letter-spacing: -0.3px;
  }
  .benefit {
    position: absolute; top: 846px; width: 230px; text-align: center; color: var(--white);
    font-weight: 700; font-size: 21px; line-height: 1.2;
  }
  .benefit svg { display: block; margin: 0 auto 6px; }
  .benefit-job { left: 56px; }
  .benefit-business { left: 288px; }
  .benefit-salary { left: 518px; }
  .col-rule { position: absolute; top: 838px; width: 1px; height: 130px; background: #555; }

  .topics {
    position: absolute; left: 0; top: 1021px; width: 800px; text-align: center;
    color: var(--white); font-weight: 400; font-size: 11px; line-height: 1.42; text-transform: uppercase;
  }
  .topics span { display: block; white-space: nowrap; }
</style>
</head>
<body>
<main class="poster">
  <div class="hero-photo" role="img" aria-label="Photograph of a professional man in a dark suit, white shirt and blue tie seated at a desk in a bright office"></div>

  <h1>
    <span class="headline"><span class="learn">LEARN</span><span class="it-light">IT</span></span>
    <span class="subline"><span class="light">TO </span><span class="bold">EARN</span><span class="light"> IT</span></span>
  </h1>

  <div class="divider"></div>

  <h2 class="course-title">
    <span class="line-lg">BUSINESS</span>
    <span class="line-md">ENRICHMENT</span>
    <span class="line-course">COURSE</span>
  </h2>
  <p class="since">Since 2005</p>

  <section class="info-band"></section>
  <div class="benefits-frame"></div>
  <div class="benefits-label">A PROVEN SUCCESS OF HELPING PEOPLE</div>

  <div class="col-rule" style="left:283px"></div>
  <div class="col-rule" style="left:517px"></div>

  <div class="benefit benefit-job">
    <svg width="62" height="62" viewBox="0 0 62 62" aria-hidden="true">
      <circle cx="31" cy="31" r="29" fill="var(--icon-fill)" stroke="var(--icon-ring)" stroke-width="2"/>
      <circle cx="31" cy="28" r="9" fill="none" stroke="#fff" stroke-width="1.8"/>
      <path d="M25 36 l-3 11 5-2 3 4 1-9 M37 36 l3 11 -5-2 -3 4 -1-9" fill="none" stroke="#fff" stroke-width="1.6" stroke-linejoin="round"/>
      <path d="M22 16 h18" stroke="#fff" stroke-width="1.8"/>
    </svg>
    Get a<br>quality job
  </div>

  <div class="benefit benefit-business">
    <svg width="62" height="62" viewBox="0 0 62 62" aria-hidden="true">
      <circle cx="31" cy="31" r="29" fill="var(--icon-fill)" stroke="var(--icon-ring)" stroke-width="2"/>
      <rect x="17" y="36" width="5" height="8" fill="none" stroke="#fff" stroke-width="1.6"/>
      <rect x="25" y="32" width="5" height="12" fill="none" stroke="#fff" stroke-width="1.6"/>
      <rect x="33" y="28" width="5" height="16" fill="none" stroke="#fff" stroke-width="1.6"/>
      <rect x="41" y="23" width="5" height="21" fill="none" stroke="#fff" stroke-width="1.6"/>
      <path d="M17 29 l9-6 6 3 12-10 M39 16 h5 v5" fill="none" stroke="#fff" stroke-width="1.6"/>
    </svg>
    Start/grow<br>a business
  </div>

  <div class="benefit benefit-salary">
    <svg width="62" height="62" viewBox="0 0 62 62" aria-hidden="true">
      <circle cx="31" cy="31" r="29" fill="var(--icon-fill)" stroke="var(--icon-ring)" stroke-width="2"/>
      <rect x="16" y="32" width="30" height="13" fill="none" stroke="#fff" stroke-width="1.6"/>
      <circle cx="31" cy="38.5" r="3" fill="none" stroke="#fff" stroke-width="1.4"/>
      <path d="M18 28 h26 M20 24 l8-5 5 3 11-7 M40 15 h4 v4" fill="none" stroke="#fff" stroke-width="1.6"/>
    </svg>
    Increase<br>their salary
  </div>

  <p class="topics">
    <span>Business Admiistration | Small Business Management | Finance | Investments | Computers | Accounting</span>
    <span>Sales | Marketing | Project Management Interviewing Skills | Business Law | Negotiation | Public Speaking</span>
    <span>Import/Export | Information Technoloy | Distribution | Marketing | LedgerPro | Real Estate</span>
    <span>Health Care-Management | Online Stores</span>
  </p>
</main>
</body>
</html>
```